Zvo Klinieken website for a maxillofacial surgery clinic

It's a website for a clinic for maxillofacial surgery in WordPress . The website doesn't need to be complicated but has to look professional. It needs to be in Dutch so i can give the texts. Similar websites are www.tandartsenpraktijkveldorm.nl or www.pbtspecialisten.nl. Pages would be sort of similar to https://hetcentrumvoorgezichtszorg.nl/ or https://wervelmondclinics.nl/. Those lasts are maxillofacial surgery clinic websites, but there are little more extensive.
I uploaded the logo. If this is not the proper quality i can upload the eps. Logo was made through pixelforum.

Target Market(s)

Patients who can find me and see information about the clinic

Industry/Entity Type

Healthcare

Coding

Coded - Design and coding required

Number of Pages Required

5+ page

Font styles to use
Other font styles liked:
• Something standard professional

Colors
0054AA
0677BA
7BADD7
CADEEF
E8F1F8

Requirements
Nice to have
• Something in line with the logo. I prefer a little dark like the darker logos but I'm not sure if that's professional. Logos bkvzo and rlpw are instances i'm registered to so they will have to be on the website too but small somewhere.

```html
<!DOCTYPE html>
<html lang="nl">
<head>
<meta charset="utf-8">
<title>Zvo Klinieken – Kaakchirurgie</title>
<link href="https://fonts.googleapis.com/css2?family=Fira+Sans:wght@400;500;600&family=Nunito+Sans:ital,wght@0,400;0,600;0,700;0,800;1,400&display=swap" rel="stylesheet">
<style>
:root{
  --cyan:#2aa7df;
  --cyan-soft:#d8eef9;
  --navy:#1d2b45;
  --navy-deep:#141b38;
  --navy-bar:#1f2742;
  --text:#2c3446;
  --muted:#8a909c;
  --light:#f1f2f5;
  --line:#e3e6ec;
  --star:#f08a24;
  --white:#fff;
}
*{margin:0;padding:0;box-sizing:border-box}
html,body{width:1200px;height:5220px;overflow:hidden}
body{font-family:"Nunito Sans",sans-serif;color:var(--text);background:var(--white);position:relative}
.abs{position:absolute}
h1,h2,h3,.heading{font-family:"Fira Sans",sans-serif;font-weight:500;color:var(--navy)}
.eyebrow{font-size:10px;font-weight:800;color:var(--cyan);letter-spacing:.3px;text-transform:uppercase}
.center{left:0;width:1200px;text-align:center}
.lead{font-size:13px;line-height:24px;color:var(--muted)}

/* header */
.site-header{position:absolute;top:0;left:0;width:1200px;height:126px;background:var(--white)}
.contact-chip{position:absolute;top:20px;display:flex;align-items:center;gap:9px;font-size:10px;line-height:13px}
.contact-chip b{font-weight:700;color:var(--navy)}
.contact-chip span{color:var(--muted);font-size:9px}
.chip-icon{width:28px;height:28px;border-radius:50%;background:var(--navy);display:flex;align-items:center;justify-content:center}
.brand{position:absolute;display:flex;align-items:center;gap:8px;font-family:"Nunito Sans",sans-serif;font-weight:700;color:var(--cyan)}
.brand i{display:block;border-radius:50%;border:3px solid var(--cyan)}
.btn-book{position:absolute;left:880px;top:14px;width:183px;height:40px;border-radius:20px;background:var(--navy);color:#fff;font-size:11px;font-weight:700;display:flex;align-items:center;justify-content:center}
.nav a{position:absolute;top:89px;font-size:12px;color:var(--navy);text-decoration:none;font-weight:600}

/* hero */
.hero{position:absolute;top:126px;left:0;width:1200px;height:762px;background:linear-gradient(100deg,#3a3e44 0%,#5a5e63 40%,#7a7670 60%,#3b3d40 100%)}
.hero-shade{position:absolute;inset:0;background:linear-gradient(90deg,rgba(15,20,30,.55),rgba(15,20,30,.15))}
.hero-kicker{position:absolute;left:81px;top:240px;color:#fff;font-family:"Fira Sans",sans-serif;font-size:22px;letter-spacing:3px;font-weight:500}
.hero h1{position:absolute;left:79px;top:290px;color:#fff;font-size:50px;font-weight:600}
.hero-rule{position:absolute;left:81px;top:370px;width:724px;height:1px;background:rgba(255,255,255,.6)}
.hero p{position:absolute;left:83px;top:405px;width:620px;color:#fff;font-size:15px;line-height:26px;font-weight:700}
.pill{position:absolute;height:38px;border-radius:19px;display:flex;align-items:center;justify-content:center;font-size:13px;font-weight:800}
.pill.cyan{background:var(--cyan);color:#fff}
.pill.white{background:#fff;color:var(--navy)}

/* features */
.feature{position:absolute;top:805px;width:320px;height:284px;background:#fff;border-radius:6px;box-shadow:0 6px 20px rgba(0,0,0,.1);text-align:center}
.feature .icon{position:absolute;left:120px;top:30px;width:80px;height:60px}
.feature h3{position:absolute;top:128px;width:100%;font-size:19px;font-weight:500;color:var(--navy)}
.feature p{position:absolute;top:165px;left:40px;width:240px;font-size:12px;line-height:26px;color:var(--muted)}

/* about */
.about-title{position:absolute;left:99px;top:1203px;font-size:34px;line-height:52px;font-weight:500}
.about-text{position:absolute;left:99px;top:1318px;width:420px;font-size:12px;line-height:25px;color:var(--muted)}
.btn-more{position:absolute;left:99px;top:1549px;width:156px;height:46px;background:var(--cyan);color:#fff;font-weight:800;font-size:15px;display:flex;align-items:center;justify-content:center;gap:10px;border-radius:3px}
.photo{position:absolute}

/* services */
.band-light{position:absolute;left:0;width:1200px;background:var(--light)}
.section-title{position:absolute;font-size:34px;font-weight:500}
.service{position:absolute;top:1928px;width:320px;height:285px;border-radius:4px}
.service-label{position:absolute;top:2186px;width:200px;height:52px;background:#fff;box-shadow:0 4px 14px rgba(0,0,0,.12);display:flex;align-items:center;justify-content:center;font-weight:700;font-size:15px;color:var(--navy)}

/* cta */
.cta{position:absolute;top:2321px;left:0;width:1200px;height:308px;background:linear-gradient(90deg,#1c2432 0%,#2c3442 45%,#3a4350 70%,#20283a 100%)}
.cta h2{position:absolute;top:108px;width:1200px;text-align:center;color:#fff;font-size:34px;line-height:42px;font-weight:500}
.cta h2 em{font-style:normal;color:var(--cyan)}
.cta-contact{position:absolute;left:351px;top:2599px;width:502px;height:54px;background:#fff;box-shadow:0 6px 16px rgba(0,0,0,.12);display:flex;align-items:center;justify-content:space-around;font-size:16px;color:var(--navy);font-weight:600;padding:0 20px}

/* testimonials */
.review{position:absolute;top:2899px;width:324px;height:264px;background:#fff;border:1px solid var(--line);text-align:center}
.avatar{position:absolute;top:2867px;width:66px;height:66px;border-radius:50%;border:3px solid #fff;box-shadow:0 2px 6px rgba(0,0,0,.15)}
.stars{position:absolute;top:54px;width:100%;color:var(--star);font-size:18px;letter-spacing:8px}
.review p{position:absolute;top:100px;left:50px;width:224px;font-size:13px;line-height:24px;color:var(--muted)}
.quote-badge{position:absolute;top:3123px;width:72px;height:40px;border-radius:36px 36px 0 0;background:var(--navy);color:#fff;font-family:Georgia,serif;font-size:34px;font-weight:700;text-align:center;line-height:52px}
.reviewer{position:absolute;top:3194px;width:324px;text-align:center}
.reviewer b{display:block;font-size:17px;color:var(--navy);font-weight:700;font-family:"Fira Sans",sans-serif;font-weight:500}
.reviewer span{font-size:12px;color:var(--muted)}

/* solutions */
.solutions{position:absolute;top:3300px;left:0;width:1200px;height:602px;background:linear-gradient(100deg,#7f8a93 0%,#a9b1b7 35%,#9a958f 60%,#6f747a 100%)}
.solutions-card{position:absolute;left:91px;top:3365px;width:509px;height:466px;background:#fff;border-radius:6px}
.sol-item{position:absolute;left:50px;display:flex;gap:22px}
.sol-item svg{flex:none;margin-top:4px}
.sol-item b{display:block;font-size:12px;font-weight:800;color:var(--navy);margin-bottom:6px}
.sol-item span{display:block;font-size:12px;line-height:24px;color:var(--muted);width:340px}

/* contact form */
.form-card{position:absolute;left:140px;top:4119px;width:912px;height:476px;background:#fff;border-radius:10px;box-shadow:0 4px 24px rgba(0,0,0,.08)}
.field{position:absolute;border:1.5px solid var(--cyan);border-radius:22px;height:42px}
.field.filled{background:var(--cyan-soft)}
.field label{position:absolute;top:-9px;left:30px;background:#fff;padding:0 6px;font-size:11px;font-weight:700;color:var(--navy)}
.field.filled label{background:linear-gradient(#fff 50%,var(--cyan-soft) 50%)}
.field span{position:absolute;top:20px;left:34px;font-size:11px;font-style:italic;color:var(--muted)}
.social-round{position:absolute;top:4512px;width:30px;height:30px;border-radius:50%;border:1.5px solid var(--cyan)}
.btn-send{position:absolute;left:843px;top:4508px;width:143px;height:40px;border-radius:20px;background:var(--cyan);color:#fff;font-weight:800;font-size:12px;display:flex;align-items:center;padding-left:18px}
.btn-send i{position:absolute;right:6px;top:6px;width:28px;height:28px;border-radius:50%;background:#fff;display:flex;align-items:center;justify-content:center}

/* footer */
.site-footer{position:absolute;top:4662px;left:0;width:1200px;height:497px;background:var(--navy-deep);color:#fff}
.social-sq{position:absolute;top:117px;width:34px;height:34px;border-radius:3px}
.to-top{position:absolute;left:970px;top:114px;display:flex;align-items:center;gap:22px;font-size:14px;font-weight:700}
.to-top i{width:44px;height:42px;background:var(--cyan);display:flex;align-items:center;justify-content:center}
.footer-rule{position:absolute;left:83px;top:174px;width:1034px;height:1px;background:rgba(255,255,255,.25)}
.site-footer h2{position:absolute;top:240px;width:1200px;text-align:center;color:#fff;font-size:28px;font-weight:500}
.site-footer .lead{position:absolute;top:294px;width:1200px;text-align:center;color:#fff;font-size:15px;line-height:26px}
.f-contact{position:absolute;top:378px;display:flex;gap:12px;align-items:center;font-size:14px;line-height:22px}
.f-contact b{display:block;font-weight:800}
.f-sep{position:absolute;top:378px;width:1px;height:48px;background:rgba(255,255,255,.35)}
.bottom-bar{position:absolute;top:5159px;left:0;width:1200px;height:61px;background:var(--navy-bar);color:#fff;font-size:12px;font-weight:600}
.bottom-bar span{position:absolute;top:22px}
</style>
</head>
<body>

<!-- header -->
<header class="site-header">
  <div class="contact-chip" style="left:122px">
    <div class="chip-icon"><svg width="14" height="14" viewBox="0 0 24 24"><path fill="#fff" d="M6.6 10.8a15.1 15.1 0 0 0 6.6 6.6l2.2-2.2c.3-.3.7-.4 1-.2 1.1.4 2.3.6 3.6.6.6 0 1 .4 1 1V20c0 .6-.4 1-1 1A17 17 0 0 1 3 4c0-.6.4-1 1-1h3.5c.6 0 1 .4 1 1 0 1.2.2 2.4.6 3.6.1.3 0 .7-.2 1z"/></svg></div>
    <div><b>Doe een oproep:</b><br><span>020 555 0147</span></div>
  </div>
  <div class="contact-chip" style="left:280px">
    <div class="chip-icon"><svg width="14" height="12" viewBox="0 0 24 18"><rect x="1" y="1" width="22" height="16" rx="2" fill="#fff"/><path d="M2 2l10 8 10-8" stroke="#1d2b45" stroke-width="2" fill="none"/></svg></div>
    <div><b>Email:</b><br><span>balie@zvoklinieken.nl</span></div>
  </div>
  <div class="brand" style="left:528px;top:30px;font-size:22px;line-height:24px;width:150px;flex-direction:column;gap:0;text-align:center">
    <span>Zvo</span><span style="font-size:16px">Klinieken</span>
  </div>
  <div class="btn-book">MAAK EEN AFSPRAAK</div>
  <div class="abs" style="left:880px;top:69px;width:183px;height:1px;background:var(--line)"></div>
  <nav class="nav">
    <a style="left:124px">Thuis</a>
    <a style="left:237px">Behandelingen</a>
    <a style="left:387px">Vergoeding</a>
    <a style="left:705px">Ons team</a>
    <a style="left:833px">Folders</a>
    <a style="left:957px">Contact Us</a>
  </nav>
</header>

<!-- hero -->
<section class="hero" role="img" aria-label="Kaakchirurg behandelt een patiënt in de behandelstoel">
  <div class="hero-shade"></div>
  <div class="hero-kicker">KAAKCHIRURGIE</div>
  <h1>Precisiechirurgie, Persoonlijke Zorg</h1>
  <div class="hero-rule"></div>
  <p>Lorem ipsum dolor sit amet, consectetur adipiscing elit et dolore conser tempor incididunt ut labore et dolore magna</p>
  <div class="pill cyan" style="left:83px;top:490px;width:144px">MEER LEREN</div>
  <div class="pill white" style="left:239px;top:490px;width:213px">MAAK EEN AFSPRAAK</div>
</section>

<!-- features -->
<div class="feature" style="left:91px">
  <svg class="icon" viewBox="0 0 80 60"><circle cx="30" cy="28" r="24" fill="var(--cyan-soft)"/><g stroke="var(--cyan)" stroke-width="2.2" fill="none" stroke-linecap="round"><circle cx="40" cy="20" r="6"/><path d="M28 48l8-18 10 6-6 12M24 50h32"/></g></svg>
  <h3>Klantgericht</h3>
  <p>Lorem ipsum dolor sit amet, consect adipiscing elit, sed do eiusmod tempor incididunt ut labore et dolore</p>
</div>
<div class="feature" style="left:442px">
  <svg class="icon" viewBox="0 0 80 60"><circle cx="30" cy="28" r="24" fill="var(--cyan-soft)"/><g stroke="var(--cyan)" stroke-width="2.2" fill="none" stroke-linecap="round"><path d="M26 44a16 16 0 1 1 28 0"/><path d="M40 34l6-8M30 30h2M48 30h2M40 20v2"/></g></svg>
  <h3>Professioneel</h3>
  <p>Lorem ipsum dolor sit amet, consect adipiscing elit, sed do eiusmod tempor incididunt ut labore et dolore</p>
</div>
<div class="feature" style="left:786px">
  <svg class="icon" viewBox="0 0 80 60"><circle cx="30" cy="28" r="24" fill="var(--cyan-soft)"/><path d="M44 14l5 11 12 1-9 8 3 12-11-6-11 6 3-12-9-8 12-1z" stroke="var(--cyan)" stroke-width="2.2" fill="none" stroke-linejoin="round"/></svg>
  <h3>Expertise</h3>
  <p>Lorem ipsum dolor sit amet, consect adipiscing elit, sed do eiusmod tempor incididunt ut labore et dolore</p>
</div>

<!-- about -->
<div class="eyebrow abs" style="left:99px;top:1182px">Bekijk het verschil —</div>
<h2 class="about-title">Jouw Reis naar Gezichts-<br>harmonie Begint Hier</h2>
<p class="about-text">Lorem ipsum dolor sit amet, consectetur adipiscing elit, sed do eius od tempor incididunt ut labore et dolore magna aliqua. Ut enim ad minim veniam, quis nostrud exercitation ullamco laboris nisi ut ali quip ex ea commodo consequat. Duis aute irure dolor in re prehenderit in voluptate velit esse cillum dolore eu fugiat nulla pariatur. Excepteur sint occaecat cupidatat non proident, sunt in culpa qui officia deserunt mollit anim id est laborum pariatur. Exce pteur sint occaecat cupidatat non proident, sunt in culpa qui</p>
<div class="btn-more">Meer Leren <svg width="16" height="12" viewBox="0 0 16 12"><path d="M1 6h13M9 1l5 5-5 5" stroke="#fff" stroke-width="2" fill="none"/></svg></div>
<div class="photo" role="img" aria-label="Team van kaakchirurgen met een lachende jonge patiënt in de behandelkamer" style="left:608px;top:1186px;width:497px;height:406px;background:linear-gradient(135deg,#c9dbe6 0%,#e9eef1 40%,#9fc0d4 75%,#5e86a4 100%);border-radius:4px"></div>
<svg class="abs" style="left:530px;top:1290px" width="160" height="160" viewBox="0 0 160 160"><circle cx="80" cy="80" r="74" fill="none" stroke="#9aa3b0" stroke-width="1.5" stroke-dasharray="3 4"/><circle cx="80" cy="80" r="48" fill="none" stroke="#9aa3b0" stroke-width="1" stroke-dasharray="3 4" opacity=".6"/><circle cx="80" cy="80" r="28" fill="#fff"/><circle cx="80" cy="80" r="12" fill="none" stroke="var(--cyan)" stroke-width="2"/></svg>

<!-- services -->
<section class="band-light" style="top:1666px;height:655px"></section>
<div class="eyebrow abs center" style="top:1747px">— Onze Diensten —</div>
<h2 class="section-title center" style="top:1770px">Onze Diensten</h2>
<p class="lead abs center" style="top:1834px;left:300px;width:600px">Lorem ipsum dolor sit amet, consectetur adipiscing elit, sed do eiusod tempor incididunt ut la bore et dolore magna aliqua. Ut enim ad minim veniam, quis nostrud exercitation</p>
<div class="service" role="img" aria-label="Lachend kind in de behandelstoel" style="left:93px;background:linear-gradient(160deg,#5f8aa3,#c9b7a5 60%,#ece4dc)"></div>
<div class="service" role="img" aria-label="Vrouw in de behandelstoel tijdens een consult" style="left:442px;background:linear-gradient(160deg,#8fb6cf,#c99a46 60%,#5d7e93)"></div>
<div class="service" role="img" aria-label="Chirurg behandelt een patiënt" style="left:788px;background:linear-gradient(160deg,#d7dee4,#5477a6 55%,#2c3f5e)"></div>
<div class="service-label" style="left:152px">Kaakchirurgie</div>
<div class="service-label" style="left:502px">Slaapgeneeskunde</div>
<div class="service-label" style="left:844px">Plastische Chirurgie</div>

<!-- cta -->
<section class="cta" role="img" aria-label="Gedempte foto van een behandelkamer">
  <h2>Wij zijn <em>24/7</em> bereikbaar om snel te reageren<br>op uw tandheelkundige behoeften.</h2>
</section>
<div class="cta-contact"><span>+31 20 555 0199</span><span>[or]</span><span>info@zvoklinieken.nl</span></div>

<!-- testimonials -->
<section class="band-light" style="top:2653px;height:647px"></section>
<div class="eyebrow abs center" style="top:2690px">— Getuigenissen —</div>
<h2 class="section-title center" style="top:2712px">Wat Klanten Zeggen</h2>
<p class="lead abs center" style="top:2774px;left:300px;width:600px">Lorem ipsum dolor sit amet, consectetur adipiscing elit, sed do eiusod tempor incididunt ut la bore et dolore magna aliqua. Ut enim ad minim veniam, quis nostrud exercitation</p>

<div class="review" style="left:91px"><div class="stars">★★★★★</div><p>Lorem ipsum dolor sit amet, consectetur adipiscing elit, sed do eiusmod tempor incididunt ut labore et dolore</p></div>
<div class="review" style="left:442px"><div class="stars">★★★★★</div><p>Lorem ipsum dolor sit amet, consectetur adipiscing elit, sed do eiusmod tempor incididunt ut labore et dolore</p></div>
<div class="review" style="left:793px"><div class="stars">★★★★★</div><p>Lorem ipsum dolor sit amet, consectetur adipiscing elit, sed do eiusmod tempor incididunt ut labore et dolore</p></div>
<div class="avatar" role="img" aria-label="Portret van een patiënte" style="left:220px;background:linear-gradient(160deg,#e8b07a,#3f6ea0)"></div>
<div class="avatar" role="img" aria-label="Portret van een jonge patiënt" style="left:571px;background:linear-gradient(160deg,#f2a5a5,#6e5a52)"></div>
<div class="avatar" role="img" aria-label="Portret van een patiënte" style="left:922px;background:linear-gradient(160deg,#f1ece7,#c9b9ad)"></div>
<div class="quote-badge" style="left:218px">“</div>
<div class="quote-badge" style="left:569px">“</div>
<div class="quote-badge" style="left:920px">“</div>
<div class="reviewer" style="left:91px"><b>Daan Verhoef</b><span>Brussels</span></div>
<div class="reviewer" style="left:442px"><b>Daan Verhoef</b><span>Brussels</span></div>
<div class="reviewer" style="left:793px"><b>Daan Verhoef</b><span>Brussels</span></div>

<!-- solutions -->
<section class="solutions" role="img" aria-label="Oudere patiënt in de behandelstoel met een arts op de achtergrond"></section>
<div class="solutions-card">
  <div class="eyebrow abs" style="left:52px;top:60px">Bekijk het verschil —</div>
  <h2 class="abs" style="left:51px;top:80px;font-size:34px">Gevorderde Oplossingen</h2>
  <div class="sol-item" style="top:145px">
    <svg width="30" height="30" viewBox="0 0 30 30"><g stroke="var(--cyan)" stroke-width="1.8" fill="none" stroke-linecap="round"><circle cx="17" cy="7" r="4"/><path d="M9 24l5-11 7 4-4 7M5 26h20"/></g></svg>
    <div><b>Persoonlijke Aanpak</b><span>Lorem ipsum dolor sit amet, consectetur adipiscing elit, od tempor incididunt ut labore et dolore magna</span></div>
  </div>
  <div class="sol-item" style="top:238px">
    <svg width="30" height="30" viewBox="0 0 30 30"><path d="M15 3l3.6 7.6 8.4.9-6.2 5.6 1.7 8.3L15 21.2 7.5 25.4l1.7-8.3L3 11.5l8.4-.9z" stroke="var(--cyan)" stroke-width="1.8" fill="none" stroke-linejoin="round"/></svg>
    <div><b>Bewezen Track Record</b><span>Lorem ipsum dolor sit amet, consectetur adipiscing elit, od tempor incididunt ut labore et dolore magna</span></div>
  </div>
  <div class="sol-item" style="top:330px">
    <svg width="30" height="30" viewBox="0 0 30 30"><g stroke="var(--cyan)" stroke-width="1.8" fill="none" stroke-linecap="round"><path d="M5 24a11 11 0 1 1 20 0"/><path d="M15 17l4-5"/></g></svg>
    <div><b>Kwaliteitsborging</b><span>Lorem ipsum dolor sit amet, consectetur adipiscing elit, od tempor incididunt ut labore et dolore magna</span></div>
  </div>
</div>

<!-- contact -->
<div class="eyebrow abs center" style="top:3953px;font-size:11px">—&nbsp;&nbsp;&nbsp;&nbsp;Our form&nbsp;&nbsp;&nbsp;&nbsp;—</div>
<h2 class="section-title center" style="top:3975px">Kom Met Ons In Contact</h2>
<p class="lead abs center" style="top:4038px;left:300px;width:600px">Lorem ipsum dolor sit amet, consectetur adipiscing elit, sed do eiusod tempor incididunt ut la bore et dolore magna aliqua. Ut enim ad minim veniam, quis nostrud exercitation</p>
<div class="form-card"></div>
<div class="field filled" style="left:193px;top:4181px;width:394px"><label>Voornaam</label><span>Type Name</span></div>
<div class="field" style="left:605px;top:4181px;width:394px"><label>Achternaam</label><span>Type Name</span></div>
<div class="field" style="left:193px;top:4256px;width:394px"><label>Telefoon</label><span>123 456 789</span></div>
<div class="field" style="left:605px;top:4256px;width:394px"><label>Your Email</label><span>naam@voorbeeld.nl</span></div>
<div class="field" style="left:193px;top:4331px;width:806px;height:150px;border-radius:14px"><label>Bericht</label><span>Type Message</span></div>
<div class="social-round" style="left:207px"></div>
<div class="social-round" style="left:245px"></div>
<div class="social-round" style="left:283px"></div>
<div class="social-round" style="left:321px"></div>
<div class="btn-send">Verzenden<i><svg width="12" height="12" viewBox="0 0 12 12"><path d="M4 2l4 4-4 4" stroke="var(--cyan)" stroke-width="2" fill="none"/></svg></i></div>

<!-- footer -->
<footer class="site-footer">
  <div class="social-sq" style="left:88px;background:#3a5a9c"></div>
  <div class="social-sq" style="left:137px;background:#2f6fb0"></div>
  <div class="social-sq" style="left:186px;background:#2aa7df"></div>
  <div class="social-sq" style="left:235px;background:#e0262b"></div>
  <div class="brand" style="left:525px;top:60px;font-size:30px;line-height:32px;width:150px;flex-direction:column;gap:0;text-align:center">
    <span>Zvo</span><span style="font-size:20px">Klinieken</span>
  </div>
  <div class="to-top">Naar boven<i><svg width="18" height="12" viewBox="0 0 18 12"><path d="M2 10l7-7 7 7" stroke="#fff" stroke-width="2.4" fill="none"/></svg></i></div>
  <div class="footer-rule"></div>
  <h2>Ontvang vandaag een gratis beoordeling</h2>
  <p class="lead">Lorem ipsum dolor sit amet, consectetur adipiscing elit, sed do eiusod tempor<br>incididunt ut labore et dolore magna aliqua.</p>
  <div class="f-contact" style="left:236px">
    <svg width="36" height="44" viewBox="0 0 36 44"><rect x="8" y="2" width="20" height="40" rx="3" stroke="var(--cyan)" stroke-width="2" fill="none"/><path d="M15 36h6M3 16v10M33 16v10" stroke="var(--cyan)" stroke-width="2"/></svg>
    <div>Doe een oproep<b>+31 20 555 0123</b></div>
  </div>
  <div class="f-sep" style="left:448px"></div>
  <div class="f-contact" style="left:476px">
    <svg width="48" height="44" viewBox="0 0 48 44"><rect x="3" y="12" width="42" height="30" rx="2" stroke="var(--cyan)" stroke-width="2" fill="none"/><path d="M4 13l20 16 20-16M12 12V4h24v8" stroke="var(--cyan)" stroke-width="2" fill="none"/></svg>
    <div>Mail ons op<b>contact@zvoklinieken.nl</b></div>
  </div>
  <div class="f-sep" style="left:728px"></div>
  <div class="f-contact" style="left:756px">
    <svg width="44" height="44" viewBox="0 0 44 44"><path d="M22 4a10 10 0 0 1 10 10c0 8-10 18-10 18S12 22 12 14A10 10 0 0 1 22 4z" stroke="var(--cyan)" stroke-width="2" fill="none"/><circle cx="22" cy="14" r="4" stroke="var(--cyan)" stroke-width="2" fill="none"/><path d="M6 40l6-10h6M38 40l-6-10h-6M6 40h32" stroke="var(--cyan)" stroke-width="2" fill="none"/></svg>
    <div>Locatie<b>Lindengracht 48</b></div>
  </div>
</footer>
<div class="bottom-bar">
  <span style="left:86px">Zvo Klinieken</span>
  <span style="left:689px">Privacyverklaring</span>
  <span style="left:833px">Algemene voorwaarden</span>
  <span style="left:1013px">Overzicht van de site</span>
</div>

</body>
</html>
```